Spring Detox sale graphics for social media

You MUST read the Brief in the WORD document and follow the instructions there. I want to create 10 social media graphics (new Instagram size 4:5 (1080 x 1350 pixels) focusing on our Mother’s Day Spring Detox Sale graphics, using any of the pics attached. Use the attached pics, NO RANDOM STOCK PHOTOGRAPHY. For the color scheme of the graphics, they should all be complementary to the product colors or feel like Spring time.

Target Market(s)

primarily women

Requirements
Must have
• the photos and text attached

```html
<!DOCTYPE html>
<html lang="en">
<head>
<meta charset="utf-8">
<title>Mother's Day Spring Detox Sale – Social Set</title>
<link href="https://fonts.googleapis.com/css2?family=Playfair+Display:ital,wght@0,400;0,500;0,600;1,400&family=Plus+Jakarta+Sans:wght@500;600;700;800&display=swap" rel="stylesheet">
<style>
:root{
  --board:#181818;
  --white:#ffffff;
  --ink:#1d1b1a;
  --blue:#2f7be8;
  --blue-soft:#8dbaf7;
  --blue-deep:#3a76e0;
  --green-deep:#1f5a2a;
  --green-olive:#7fa21c;
  --yellow:#f5d21c;
  --magenta:#b8206a;
  --coral:#f0645c;
  --red:#e8352f;
  --green-pill:#1a9a3c;
  --cream:#fdfcf3;
  --serif:'Playfair Display', Georgia, serif;
  --sans:'Plus Jakarta Sans', Arial, sans-serif;
}
*{margin:0;padding:0;box-sizing:border-box}
html,body{width:779px;height:1200px;overflow:hidden;background:var(--board)}
.board{position:relative;width:779px;height:1200px;background:var(--board)}
.tile{position:absolute;width:215px;height:268px;overflow:hidden}
.abs{position:absolute}
.ph{position:absolute}
.serif{font-family:var(--serif)}
.sans{font-family:var(--sans)}
.center{left:0;right:0;text-align:center}

/* 1 */
.t-mothers-flower{left:282px;top:50px;background:linear-gradient(160deg,#c9d8ef 0%,#cdb7e2 30%,#f2c4b8 65%,#f6dcc0 100%)}
.t-mothers-flower .headline{color:var(--white);font-family:var(--sans);font-weight:800;letter-spacing:-1px}
.t-mothers-flower .sale-stack{left:15px;top:148px;font-size:28px;line-height:31px;color:var(--white);font-family:var(--sans);font-weight:800;letter-spacing:-1px}
.badge-box{background:var(--magenta);color:var(--white);font-family:var(--serif);font-size:13px;text-align:center;line-height:22px;border-radius:2px}

/* 2 */
.t-feel-amazing{left:59px;top:189px;background:var(--cream)}
/* 3 */
.t-refresh{left:505px;top:189px;background:linear-gradient(150deg,#fbf7d2 0%,#f7f8ec 45%,#d9efb4 100%)}
/* 4 */
.t-framed{left:282px;top:327px;background:linear-gradient(165deg,#f7d2bb 0%,#f5c7b2 60%,#f3b7a2 100%)}
/* 5 */
.t-everything{left:59px;top:466px;background:linear-gradient(180deg,#8fbdf8,#84b6f7)}
/* 6 */
.t-shine{left:505px;top:466px;background:linear-gradient(180deg,#cfe0f1 0%,#f3f2e6 55%,#f6f7f5 100%)}
/* 7 */
.t-cleanse{left:59px;top:743px;background:linear-gradient(160deg,#fbfbf7 0%,#eef3fa 100%)}
/* 8 */
.t-supplements{left:282px;top:604px;background:#fbeacd}
/* 9 */
.t-summer-body{left:505px;top:743px;background:linear-gradient(150deg,#f7f8e6 0%,#fdfdf6 50%,#f8f1ee 100%)}
/* 10 */
.t-reset{left:282px;top:881px;background:linear-gradient(170deg,#f7d6cf 0%,#f9e2da 45%,#f2d7e8 100%)}

.flower-badge{border-radius:50%;display:flex;align-items:center;justify-content:center;text-align:center;font-family:var(--serif);line-height:0.95}
.ribbon{position:absolute;left:-40px;width:320px;height:14px;background:var(--blue-deep);color:var(--white);font-family:var(--sans);font-size:7px;font-weight:600;line-height:14px;white-space:nowrap;overflow:hidden}
</style>
</head>
<body>
<main class="board">

  <!-- 1 Mother's Day flower -->
  <section class="tile t-mothers-flower">
    <div class="ph" role="img" aria-label="Red and peach lily stem" style="left:55px;top:55px;width:100px;height:213px;background:radial-gradient(ellipse at 50% 30%,#f07a55 0%,#f4a48a 35%,rgba(244,180,160,0) 70%)"></div>
    <div class="ph" role="img" aria-label="Detox supplement bottle" style="left:140px;top:140px;width:55px;height:75px;border-radius:8px;transform:rotate(-18deg);background:linear-gradient(180deg,#f4f4f6,#e6d7e6)"></div>
    <div class="abs headline" style="left:15px;top:20px;font-size:32px">Mother’s</div>
    <div class="abs headline" style="left:138px;top:98px;font-size:32px">Day</div>
    <div class="abs sale-stack">SPRING<br>DETOX<br>SALE</div>
    <div class="abs badge-box" style="left:135px;top:218px;width:63px;height:22px">25% OFF</div>
    <div class="abs serif" style="left:135px;top:242px;font-size:12px;color:var(--magenta)">Everything!</div>
  </section>

  <!-- 2 Feel amazing -->
  <section class="tile t-feel-amazing">
    <div class="ph" role="img" aria-label="Soft pastel blossoms" style="left:0;top:0;width:60px;height:120px;background:radial-gradient(ellipse at 20% 30%,#f5c3cf 0%,#cbdcf0 40%,rgba(253,252,243,0) 75%)"></div>
    <div class="ph" role="img" aria-label="Soft pastel blossoms" style="left:100px;top:190px;width:115px;height:78px;background:radial-gradient(ellipse at 70% 70%,#f5c9a9 0%,#c7c4ee 40%,rgba(253,252,243,0) 75%)"></div>
    <div class="abs serif" style="left:40px;top:52px;font-size:34px;color:var(--blue);letter-spacing:-1px">25% OFF</div>
    <div class="abs serif" style="left:43px;top:94px;font-size:26px;color:var(--ink);letter-spacing:-1px">MOTHER’S</div>
    <div class="abs serif" style="left:52px;top:119px;font-size:26px;letter-spacing:-1px"><span style="color:var(--ink)">DAY</span> <span style="color:var(--blue)">SALE</span></div>
    <svg class="abs" style="left:35px;top:152px" width="145" height="8"><line x1="2" y1="4" x2="143" y2="4" stroke="#1d1b1a" stroke-width="1"/><circle cx="72" cy="4" r="2" fill="none" stroke="#1d1b1a"/><circle cx="2" cy="4" r="1.5" fill="#1d1b1a"/><circle cx="143" cy="4" r="1.5" fill="#1d1b1a"/></svg>
    <div class="abs center sans" style="top:166px;font-size:18px;line-height:21px;font-weight:800;color:var(--blue);letter-spacing:-0.5px">FEEL AMAZING<br>AGAIN!</div>
  </section>

  <!-- 3 Refresh -->
  <section class="tile t-refresh">
    <div class="ph" role="img" aria-label="Yellow tulips" style="left:0;top:120px;width:70px;height:148px;background:radial-gradient(ellipse at 40% 30%,#f1dc4e 0%,rgba(241,220,78,0) 65%)"></div>
    <div class="ph" role="img" aria-label="Hormone supplement bottle" style="left:125px;top:50px;width:72px;height:110px;border-radius:10px;transform:rotate(15deg);background:linear-gradient(180deg,#ffffff,#e6efeb)"></div>
    <div class="abs flower-badge" style="left:20px;top:18px;width:62px;height:62px;background:var(--yellow);font-size:18px;color:var(--green-deep)">25%<br>OFF</div>
    <div class="abs sans" style="left:20px;top:84px;font-size:23px;line-height:26px;font-weight:600;color:var(--green-olive);letter-spacing:-0.5px">Mother’s</div>
    <div class="abs sans" style="left:18px;top:110px;font-size:23px;line-height:26px;font-weight:600;color:var(--green-deep);letter-spacing:-0.5px">Day Sale</div>
    <div class="abs serif" style="left:35px;top:168px;font-size:42px;font-weight:500;color:var(--green-deep);letter-spacing:-1px">Refresh</div>
    <div class="abs serif" style="left:45px;top:213px;font-size:25px;color:var(--green-olive)">Your Body</div>
  </section>

  <!-- 4 Framed products -->
  <section class="tile t-framed">
    <div class="abs center serif" style="top:24px;font-size:21px;color:var(--ink)">Mother’s Day</div>
    <div class="abs" style="left:28px;top:51px;width:158px;height:180px;border:3px solid var(--white)"></div>
    <div class="ph" role="img" aria-label="Supplement bottles with bouquet of flowers" style="left:45px;top:75px;width:160px;height:90px;background:linear-gradient(90deg,#eceef3 0%,#f3f0ee 50%,#f6d4c6 75%,#f4a040 100%);border-radius:6px"></div>
    <div class="abs" style="left:28px;top:170px;width:158px;height:61px;background:var(--white)"></div>
    <div class="abs sans" style="left:44px;top:175px;font-size:13px;line-height:14px;font-weight:800;color:var(--red)">SPRING<br>DETOX</div>
    <div class="abs serif" style="left:48px;top:200px;width:58px;height:21px;background:var(--green-pill);color:var(--white);font-size:16px;line-height:21px;text-align:center">SALE</div>
    <div class="abs" style="left:117px;top:178px;width:1px;height:44px;background:var(--ink)"></div>
    <div class="abs serif" style="left:124px;top:172px;font-size:27px;line-height:27px;color:var(--ink)">25%<br>OFF</div>
  </section>

  <!-- 5 Everything -->
  <section class="tile t-everything">
    <div class="abs flower-badge" style="left:74px;top:47px;width:66px;height:66px;background:var(--white);font-size:19px;color:var(--blue)">25%<br>OFF</div>
    <div class="abs center serif" style="top:108px;font-size:33px;color:var(--white)">Everything</div>
    <div class="abs sans" style="left:51px;top:154px;width:112px;height:25px;background:var(--blue-deep);border-radius:3px;color:var(--white);font-size:12px;font-weight:700;text-align:center;line-height:25px">MOTHER’S DAY</div>
    <div class="abs center sans" style="top:180px;font-size:19px;font-weight:800;color:var(--white);letter-spacing:-0.5px">SPRING DETOX</div>
    <div class="abs center sans" style="top:200px;font-size:30px;font-weight:800;color:var(--white)">SALE</div>
  </section>

  <!-- 6 Shine this summer -->
  <section class="tile t-shine">
    <div class="ph" role="img" aria-label="Yellow lily petals against blue sky" style="left:0;top:0;width:215px;height:150px;background:radial-gradient(ellipse at 65% 35%,#f3e6a0 0%,#e9e6c8 35%,rgba(207,224,241,0) 70%)"></div>
    <div class="ph" role="img" aria-label="Hormone supplement bottle" style="left:0;top:45px;width:55px;height:100px;border-radius:8px;transform:rotate(-20deg);background:linear-gradient(180deg,#fff,#e3ece8)"></div>
    <div class="ph" role="img" aria-label="Hormone supplement bottle" style="left:165px;top:108px;width:40px;height:65px;border-radius:6px;transform:rotate(12deg);background:linear-gradient(180deg,#fff,#e3ece8)"></div>
    <div class="abs center sans" style="top:142px;font-size:28px;font-weight:700;color:var(--green-deep);letter-spacing:-1px">25% OFF</div>
    <div class="abs center sans" style="top:172px;font-size:18px;font-weight:600;color:var(--green-deep);letter-spacing:-0.5px">Mother’s Day Sale</div>
    <svg class="abs" style="left:47px;top:198px" width="120" height="6"><line x1="0" y1="3" x2="120" y2="3" stroke="#b9c97a" stroke-width="1"/><circle cx="60" cy="3" r="1.5" fill="#b9c97a"/></svg>
    <div class="abs center sans" style="top:208px;font-size:16px;line-height:19px;font-weight:500;color:var(--green-olive)">Detox This Spring.<br>Shine This Summer.</div>
  </section>

  <!-- 7 Spring cleanse -->
  <section class="tile t-cleanse">
    <div class="ribbon" style="top:22px;transform:rotate(-10deg)">25% Off ✦ 25% Off ✦ 25% Off ✦ 25% Off ✦ 25% Off ✦ 25% Off ✦ 25% Off ✦ 25% Off</div>
    <div class="ribbon" style="top:182px;transform:rotate(9deg)">25% Off ✦ 25% Off ✦ 25% Off ✦ 25% Off ✦ 25% Off ✦ 25% Off ✦ 25% Off ✦ 25% Off</div>
    <div class="ph" role="img" aria-label="Blood sugar supplement bottle" style="left:118px;top:70px;width:70px;height:130px;border-radius:10px;transform:rotate(25deg);background:linear-gradient(180deg,#ffffff,#e1e6f3)"></div>
    <div class="abs serif" style="left:19px;top:50px;font-size:30px;line-height:27px;color:var(--blue);letter-spacing:-0.5px">Spring<br>Detox<br>Sale</div>
    <div class="abs flower-badge" style="left:73px;top:115px;width:56px;height:56px;background:var(--blue);font-family:var(--sans);font-weight:800;font-size:14px;color:var(--white)">25%<br>OFF</div>
    <div class="abs sans" style="left:19px;top:207px;font-size:20px;line-height:22px;font-weight:600;color:#3a3a3a;letter-spacing:-0.5px">Spring Cleanse.</div>
    <div class="abs sans" style="left:19px;top:229px;font-size:20px;line-height:22px;font-weight:600;color:var(--blue);letter-spacing:-0.5px">Summer Glow</div>
  </section>

  <!-- 8 All supplements -->
  <section class="tile t-supplements">
    <div class="abs center serif" style="top:17px;font-size:32px;color:var(--coral);letter-spacing:-1px">25% OFF</div>
    <div class="abs center sans" style="top:53px;font-size:13px;font-weight:800;color:var(--ink);letter-spacing:-0.3px">ALL SUPPLEMENTS</div>
    <div class="abs" style="left:52px;top:74px;width:108px;height:152px;background:var(--white);transform:rotate(2deg)"></div>
    <div class="ph" role="img" aria-label="Photo of the founder in a kitchen with the supplement range" style="left:58px;top:80px;width:96px;height:140px;transform:rotate(2deg);background:linear-gradient(180deg,#6d4a38 0%,#8a6a58 50%,#d9d3ce 100%)"></div>
    <div class="abs center serif" style="top:226px;font-size:14px;color:var(--coral)">SPRING <span style="font-size:22px">DETOX</span> SALE!</div>
  </section>

  <!-- 9 Summer body -->
  <section class="tile t-summer-body">
    <div class="ph" role="img" aria-label="Yellow tulip stems" style="left:180px;top:150px;width:35px;height:118px;background:radial-gradient(ellipse at 60% 40%,#f2e27a 0%,rgba(242,226,122,0) 70%)"></div>
    <div class="abs sans" style="left:20px;top:52px;font-size:27px;font-weight:700;color:var(--green-deep);letter-spacing:-1px">25% OFF</div>
    <div class="abs serif" style="left:20px;top:82px;font-size:28px;color:var(--green-deep);letter-spacing:-0.5px">Mother’s Day</div>
    <div class="abs serif" style="left:20px;top:113px;font-size:26px;color:var(--green-olive)">Sale.</div>
    <svg class="abs" style="left:152px;top:60px" width="22" height="22"><path d="M11 0 L13 9 L22 11 L13 13 L11 22 L9 13 L0 11 L9 9 Z" fill="var(--yellow)"/></svg>
    <svg class="abs" style="left:52px;top:185px" width="20" height="20"><path d="M10 0 L12 8 L20 10 L12 12 L10 20 L8 12 L0 10 L8 8 Z" fill="var(--yellow)"/></svg>
    <div class="abs sans" style="right:28px;top:198px;text-align:right;font-size:16px;line-height:19px;font-weight:500;color:var(--green-olive)">Spring Detox<br>For A Summer Body!</div>
  </section>

  <!-- 10 Spring reset -->
  <section class="tile t-reset">
    <div class="abs center serif" style="top:22px;font-size:32px;color:var(--magenta);letter-spacing:-1px">25% OFF</div>
    <div class="abs center sans" style="top:60px;font-size:21px;font-weight:800;color:var(--ink);letter-spacing:-0.8px">SPRING DETOX</div>
    <div class="abs sans" style="left:62px;top:82px;width:88px;height:30px;background:var(--magenta);transform:rotate(-3deg);color:var(--white);font-size:24px;font-weight:800;line-height:30px;text-align:center">SALE</div>
    <div class="ph" role="img" aria-label="Supplement bottles on a stone plinth" style="left:20px;top:112px;width:178px;height:76px;border-radius:6px;background:linear-gradient(90deg,#f2eeee 0%,#ffffff 40%,#eee5ea 70%,#f3d6dc 100%)"></div>
    <div class="abs center serif" style="top:190px;font-size:22px;color:var(--magenta)">Spring Reset.</div>
    <div class="abs center serif" style="top:215px;font-size:22px;color:var(--ink)">Summer Ready</div>
  </section>

</main>
</body>
</html>
```